Tampa Bay fishing guide needs stunning website.

I currently have a site - www.reelcoveguide.net which I personally put together using the Pagely platform and I am looking for a redesign on a different platform (Sitecraft?) that will allow me to easily create landing pages in the future. Would like to have a block for visitors to opt in to newsletter. Need social media links on all pages.

I would like to let my visitors know that I am able to handle their fishing charter needs here in the Tampa Bay area, if I'm not available for the dates they are looking to go I can refer them to a reputable captain in the area.

Target Market(s)

United States

Industry/Entity Type

Tourism

Coding

Coded - Design and coding required

Number of Pages Required

5+ page

Font styles to use
Sans Serif

Colors
0355a3
3176b5
85abd2
fbf289

Requirements
Must have
• Mobile Responsive, Ability to insert Vantor Metrics, Chatterbox pixels, ability to add custom landing pages in future
Nice to have
• Clean, easy navigation

```html
<!DOCTYPE html>
<html lang="en">
<head>
<meta charset="utf-8">
<title>Capt. Wade Harlan – Tampa Bay Fishing Charters</title>
<link rel="stylesheet" href="https://fonts.googleapis.com/css2?family=Michroma&family=Raleway:wght@400;500;600&display=swap">
<style>
:root{
  --blue-deep:#0355a3;
  --blue:#1f67d6;
  --blue-mid:#3176b5;
  --blue-soft:#85abd2;
  --blue-light:#6ea6ef;
  --yellow:#fbf289;
  --ink:#555a60;
  --muted:#8a8f95;
  --white:#ffffff;
  --paper:#e8eff9;
  --card:#f2f2f2;
  --footer:#ececec;
  --line:#c9cdd2;
}
*{box-sizing:border-box;margin:0;padding:0}
html,body{width:1200px;height:2711px;overflow:hidden}
body{font-family:"Raleway",sans-serif;color:var(--ink);background:var(--white);position:relative}
.section{position:absolute;left:0;width:1200px}
.abs{position:absolute}
.display{font-family:"Michroma",sans-serif;letter-spacing:4px}

/* hero */
.hero{top:0;height:678px;background:linear-gradient(180deg,#6fa4d8 0%,#a9c9ea 28%,#2a5f9c 42%,#163f78 70%,#0f2f5e 100%)}
.hero-photo{inset:0}
.hero-call{top:14px;right:78px;color:#cfe2fb;font-size:16px;display:flex;align-items:center;gap:10px}
.hero-call .ring{width:34px;height:34px;border:2px solid #cfe2fb;border-radius:50%;display:flex;align-items:center;justify-content:center}
.hero-brand{top:80px;left:0;width:1200px;text-align:center;font-family:"Raleway",sans-serif;font-weight:600;font-size:52px;color:var(--blue)}
.hero-title{right:80px;top:370px;width:760px;text-align:right;color:var(--white);font-size:31px;line-height:53px;letter-spacing:5px}

/* nav */
.nav{top:678px;height:52px;background:var(--blue);display:flex;padding-left:78px}
.nav a{color:#d8e7fb;text-decoration:none;font-size:15px;line-height:52px;padding:0 33px;text-transform:uppercase}
.nav a.active{background:var(--blue-light);color:var(--deep,#12306a);padding:0 55px;color:#143c7a}

/* welcome */
.welcome{top:730px;height:405px}
.section-title{width:1200px;left:0;text-align:center;font-size:34px;color:var(--blue)}
.section-title span{color:var(--blue-light)}
.welcome .section-title{top:60px}
.welcome-text{left:81px;top:144px;width:655px;font-size:15px;line-height:26px;color:var(--muted)}
.welcome-text p+p{margin-top:26px}
.welcome-brand{left:755px;top:164px;width:365px;height:130px;display:flex;align-items:center;justify-content:center;font-weight:600;font-size:42px;color:var(--blue)}
.btn{display:block;background:var(--blue);color:var(--white);text-align:center;text-transform:uppercase;font-size:20px;text-decoration:none}
.welcome .btn{left:78px;top:296px;width:208px;height:46px;line-height:46px}

/* pickup */
.pickup{top:1135px;height:573px;background:var(--paper)}
.pickup .section-title{top:38px}
.marina{top:118px;width:475px}
.marina h3{font-weight:500;font-size:27px;color:var(--blue);margin-bottom:10px}
.marina p{font-size:16px;line-height:26px;color:#a0a6ac}
.marina .map{margin-top:22px;width:475px;height:215px;background:linear-gradient(135deg,#9cc4f2 0%,#dfe6dc 45%,#eceae4 100%)}
.pickup .btn{left:497px;top:484px;width:206px;height:45px;line-height:45px}

/* testimonials */
.testimonials{top:1708px;height:419px}
.testimonials .section-title{top:68px}
.quote{top:157px;width:293px;height:218px;background:var(--card);text-align:center;padding:38px 22px 0;font-size:17px;line-height:27px;color:var(--ink)}
.quote cite{display:block;margin-top:24px;font-style:normal;font-size:16px;line-height:24px}
.arrow{top:250px}

/* newsletter */
.newsletter{top:2127px;height:125px;background:var(--blue)}
.newsletter h2{left:80px;top:30px;font-family:"Raleway",sans-serif;font-weight:400;font-size:58px;color:var(--yellow);letter-spacing:1px}
.newsletter .field{left:517px;top:41px;width:405px;height:44px;border:1.5px solid var(--yellow);color:#f2efb6;font-size:16px;line-height:41px;padding-left:12px}
.newsletter .subscribe{left:936px;top:41px;width:186px;height:44px;background:var(--white);color:var(--blue);font-size:21px;line-height:44px;text-align:center}

/* footer */
.footer{top:2252px;height:408px;background:var(--footer)}
.footer-brand{left:78px;top:62px;font-weight:600;font-size:24px;color:#333}
.footer-about{left:78px;top:128px;width:210px;font-size:15px;line-height:25px;color:var(--ink)}
.footer-about a{color:var(--blue);text-decoration:none}
.footer h4{top:46px;font-family:"Michroma",sans-serif;font-size:12px;letter-spacing:2px;color:#333;font-weight:400}
.contact-list{left:340px;top:90px;width:230px;font-size:14px;line-height:22px;color:var(--ink);list-style:none}
.contact-list li{display:flex;gap:16px;margin-bottom:18px}
.contact-list svg{flex:none;margin-top:2px}
.social{left:342px;top:278px;display:flex;gap:12px}
.social span{height:40px;padding:0 12px;border-radius:20px;border:2px solid #b5babf;font-size:12px;line-height:36px;color:#777}
.social span.primary{background:var(--blue);border-color:var(--blue);color:var(--white)}
.links{left:607px;top:96px;list-style:none;font-size:14px;line-height:25px;color:var(--ink)}
.form-field{left:840px;width:282px;height:40px;border:1px solid var(--line);background:#f1f1f1;font-size:14px;padding:10px 18px;color:var(--ink)}
.form-submit{left:842px;top:318px;width:155px;height:41px;line-height:41px;background:var(--blue);color:var(--white);font-size:15px;text-align:center;text-transform:uppercase}

.copyright{top:2660px;height:51px;background:var(--blue);text-align:center;color:#dce8fa;font-size:12px;line-height:51px}
</style>
</head>
<body>

<header class="section hero">
  <div class="abs hero-photo" role="img" aria-label="Photo of an angler on a boat reeling in a catch on open water under a blue sky"></div>
  <div class="abs hero-call">Call Capt. Wade
    <span class="ring"><svg width="16" height="16" viewBox="0 0 24 24" fill="none" stroke="#cfe2fb" stroke-width="2"><path d="M5 3h4l2 5-3 2a12 12 0 0 0 6 6l2-3 5 2v4a2 2 0 0 1-2 2A18 18 0 0 1 3 5a2 2 0 0 1 2-2z"/></svg></span>
    (813) 555-0142</div>
  <div class="abs hero-brand">Capt. Wade Harlan</div>
  <h1 class="abs hero-title display" style="font-weight:400">Come fish with Tampa Bay, FL fishing guide, Tampa Bay fishing charter most respected Captain, 25 year Native Guide</h1>
</header>

<nav class="section nav">
  <a class="active" href="#">Home</a>
  <a href="#">About Us</a>
  <a href="#">Pick Up Location</a>
  <a href="#">Rates</a>
  <a href="#">Contact Us</a>
  <a href="#">Gift Card</a>
</nav>

<section class="section welcome">
  <h2 class="abs section-title display" style="font-weight:400">Welcome To <span>Capt. Wade Harlan</span></h2>
  <div class="abs welcome-text">
    <p>Capt. Wade Harlan, with over 20 years' experience, Native fishing charter tampa charter captain offering full and half day fishing charters on the waters of Tampa Bay.</p>
    <p>If you're looking for a great fishing charter tampa don't hesitate to contact Capt. Wade or you can simply book your trip online here.</p>
  </div>
  <a class="abs btn" href="#">Read More</a>
  <div class="abs welcome-brand">Capt. Wade Harlan</div>
</section>

<section class="section pickup">
  <h2 class="abs section-title display" style="font-weight:400">Our <span>Pick up Location</span></h2>
  <div class="abs marina" style="left:80px">
    <h3>HARBOR POINT MARINA</h3>
    <p>4820 Gulfview Avenue South<br>St. Petersburg, FL 33711</p>
    <div class="map" role="img" aria-label="Map showing the St. Petersburg pick up marina"></div>
  </div>
  <div class="abs marina" style="left:645px">
    <h3>HARBOR POINT MARINA</h3>
    <p>27 Tidewater Ln<br>Ruskin, FL 33570</p>
    <div class="map" role="img" aria-label="Map showing the Ruskin pick up marina"></div>
  </div>
  <a class="abs btn" href="#">View All</a>
</section>

<section class="section testimonials">
  <h2 class="abs section-title display" style="font-weight:400">Our <span>Testimonial</span></h2>
  <svg class="abs arrow" style="left:28px" width="24" height="44" viewBox="0 0 24 44" fill="none" stroke="var(--blue-soft)" stroke-width="3"><path d="M20 4 4 22l16 18"/></svg>
  <blockquote class="abs quote" style="left:78px">"Capt. Wade has always been a 100%er for me"<cite>- Glen Marlowe,<br>Outdoor Editor for<br>Bay Area Ledger</cite></blockquote>
  <blockquote class="abs quote" style="left:452px">"Truly a master angler"<cite>- Ruth Calloway,<br>former Hillsborough<br>County Commissioner</cite></blockquote>
  <blockquote class="abs quote" style="left:829px">"Congratulations on winning the Gulf Coast Celebrity Grand Slam Tournament"<cite>- Dale Whitmore,</cite></blockquote>
  <svg class="abs arrow" style="left:1150px" width="24" height="44" viewBox="0 0 24 44" fill="none" stroke="var(--blue-soft)" stroke-width="3"><path d="M4 4l16 18L4 40"/></svg>
</section>

<section class="section newsletter">
  <h2 class="abs">NEWSLETTER</h2>
  <div class="abs field">Enter Email Id</div>
  <div class="abs subscribe">SUBSCRIBE</div>
</section>

<footer class="section footer">
  <div class="abs footer-brand">Capt. Wade Harlan</div>
  <p class="abs footer-about">If you're looking for a great fishing charter tampa don't hesitate to contact Capt. Wade or you can simply <a href="#">book your trip online here.</a></p>

  <h4 class="abs" style="left:345px">Contact Us</h4>
  <ul class="abs contact-list">
    <li><svg width="14" height="18" viewBox="0 0 14 18"><path d="M7 0a7 7 0 0 0-7 7c0 5 7 11 7 11s7-6 7-11a7 7 0 0 0-7-7zm0 10a3 3 0 1 1 0-6 3 3 0 0 1 0 6z" fill="#888"/></svg><span>123, Harbor Road, City,<br>Country, Zip code</span></li>
    <li><svg width="18" height="18" viewBox="0 0 24 24" fill="none" stroke="#888" stroke-width="2"><path d="M5 3h4l2 5-3 2a12 12 0 0 0 6 6l2-3 5 2v4a2 2 0 0 1-2 2A18 18 0 0 1 3 5a2 2 0 0 1 2-2z"/></svg><span>813-555-0142</span></li>
    <li><svg width="18" height="14" viewBox="0 0 18 14" fill="none" stroke="#888" stroke-width="1.6"><rect x="1" y="1" width="16" height="12"/><path d="M1 1l8 7 8-7"/></svg><span>captwade@reelcoveguide.net</span></li>
  </ul>
  <div class="abs social"><span class="primary">Chatterbox</span><span>Chirper</span><span>Circlenet</span></div>

  <h4 class="abs" style="left:607px">Usefull Links</h4>
  <ul class="abs links"><li>Home</li><li>About</li><li>Pick up Location</li><li>Rate</li><li>Contact</li><li>Gift Card</li></ul>

  <h4 class="abs" style="left:837px">Get In Touch</h4>
  <div class="abs form-field" style="top:93px">Name</div>
  <div class="abs form-field" style="top:140px">Phone</div>
  <div class="abs form-field" style="top:187px">E mail</div>
  <div class="abs form-field" style="top:234px;height:73px">Message</div>
  <div class="abs form-submit">Submit</div>
</footer>

<div class="section copyright">© Capt. Wade Harlan - 2016 All Right Reserved</div>

</body>
</html>
```